Kestrel Baseball & Softball Camp 2017

Design a flyer that will promote our 2017 summer camp for boys and girls softball.

Weeks of
July 10th - 14th
July 17th - 21st.

Players ages 5 - 11.
Full day = 9:30am - 2:30pm half day = 9:30am - 11:30am.
$295 / full day : $195/ half day

Hosted by "Kestrel Baseball" affiliated with the Harbor Comets Travel Baseball & Softball Club and the Maple Ridge Youth League,

Camp Location MRYL, Route 9C Birch Hollow.

PHone 555-240-7813, email info@kestrelball.example

The color should be "Red white and blue color scheme" with dates and location standing out. Kestrel Logo should be prominent MRYL and Comets smaller and secondary.

Feel free to use stock photo's if available. visit www.harborcomets.example for more pictures and there are links for the 2017 summer camp there with possibly some more information.

Target Market(s)

to catch the eye of parents of players ages 5 - 11 already at little league or shopping in local stores

Colors
ec1f27
0355a3
ffffff

Requirements
Must have
• red white and blue design,
• Kestrel logo and summer camp prominent so it catches the eye and explains what it is right away.
• the comets and maple ridge logo's a the bottom showing the affiliation.
Nice to have
• stock photo's or something showing players having a great time or a beautiful ballpark
Should not have
• to much clutter or hard to figure out what it's for

```html
<!DOCTYPE html>
<html lang="en">
<head>
<meta charset="utf-8">
<title>Kestrel Softball Summer Camp 2017</title>
<link rel="stylesheet" href="https://fonts.googleapis.com/css2?family=Bebas+Neue&family=Oswald:wght@500;600&family=Kaushan+Script&family=Yellowtail&display=swap">
<style>
  :root {
    --red: #d6252c;
    --red-bright: #ec1f27;
    --blue: #1f3a68;
    --blue-brand: #0355a3;
    --white: #ffffff;
    --ink: #1d1d1f;
    --rule: #9a9a9a;
    --orange: #e0572b;
  }
  * { margin: 0; padding: 0; box-sizing: border-box; }
  html, body { width: 817px; height: 1200px; overflow: hidden; background: var(--white); }
  .flyer { position: relative; width: 817px; height: 1200px; overflow: hidden; background: var(--white); font-family: "Bebas Neue", sans-serif; color: var(--ink); }
  .abs { position: absolute; }

  .hero-photo { left: 0; top: 0; width: 817px; height: 535px;
    background: linear-gradient(180deg, #2a6fc0 0%, #5d9ad8 35%, #b9d2e6 58%, #8aa9b0 70%, #4f8a3c 82%, #3d7a2e 100%); }
  .shapes { left: 0; top: 0; width: 817px; height: 1200px; }

  .brand { left: 40px; top: 95px; width: 200px; display: flex; align-items: center; gap: 10px; }
  .brand-dot { width: 26px; height: 26px; border-radius: 50%; background: var(--red-bright); flex: none; }
  .brand-name { font-size: 54px; color: var(--red-bright); line-height: 1; letter-spacing: 1px; }

  .script-softball { left: 50px; top: 318px; font-family: "Yellowtail", cursive; font-size: 62px; color: var(--red); line-height: 1; }
  .headline { left: 52px; top: 388px; font-size: 140px; line-height: 1; letter-spacing: 2px; white-space: nowrap; }
  .headline .summer { color: var(--white); }
  .headline .camp { color: var(--blue); }
  .year { left: 715px; top: 420px; font-size: 44px; color: var(--blue); line-height: 1; transform: rotate(90deg); transform-origin: left top; letter-spacing: 2px; }
  .year { left: 762px; top: 400px; }

  .audience { left: 465px; top: 542px; font-family: "Kaushan Script", cursive; font-size: 20px; color: var(--white); }

  .dates { left: 77px; top: 604px; font-size: 42px; color: var(--white); line-height: 47px; letter-spacing: 1px; }

  .ages { left: 440px; top: 640px; display: flex; align-items: flex-start; gap: 10px; }
  .ages-label { font-size: 38px; line-height: 44px; color: var(--blue); letter-spacing: 1px; }
  .ages-badge { left: 637px; top: 624px; width: 138px; height: 138px; border-radius: 50%; background: var(--blue);
    display: flex; align-items: center; justify-content: center; font-size: 44px; color: var(--white); letter-spacing: 1px; }

  .hours { left: 68px; top: 830px; display: flex; gap: 14px; align-items: center; }
  .hours-text, .cost-text { font-size: 27px; line-height: 32px; letter-spacing: .5px; }
  .hours-text { color: var(--red); }
  .cost { left: 445px; top: 830px; display: flex; gap: 10px; align-items: center; }
  .cost-label { font-family: "Kaushan Script", cursive; font-size: 20px; color: var(--blue); }
  .cost-text { color: var(--blue); }

  .rule-dashed { left: 40px; width: 740px; border-top: 2px dashed var(--rule); }
  .rule-solid { left: 40px; width: 740px; border-top: 2px solid var(--ink); }

  .hosted { left: 43px; top: 942px; font-family: "Oswald", sans-serif; font-weight: 600; font-size: 10.5px; line-height: 15px; text-transform: uppercase; color: var(--ink); letter-spacing: .2px; }
  .partner-comets { left: 525px; top: 945px; width: 125px; height: 50px; background: var(--red); border-radius: 3px; }
  .partner-league { left: 695px; top: 932px; width: 72px; height: 72px; background: #e8e8e8; border: 3px solid var(--blue-brand); }

  .register { left: 58px; top: 1068px; font-family: "Kaushan Script", cursive; font-size: 40px; line-height: 46px; color: var(--orange); transform: rotate(-8deg); }
  .block { top: 1085px; }
  .block-head { display: flex; align-items: center; gap: 10px; font-family: "Kaushan Script", cursive; font-size: 19px; color: var(--blue); margin-bottom: 10px; }
  .block-body { font-size: 21px; line-height: 26px; letter-spacing: .5px; color: var(--ink); }
  .location { left: 262px; }
  .location .block-body { padding-left: 28px; }
  .contact { left: 518px; }
  .contact .block-body { padding-left: 25px; }
</style>
</head>
<body>
<div class="flyer">
  <div class="abs hero-photo" role="img" aria-label="Smiling young softball player holding a bat and glove in a ballpark under a blue sky"></div>

  <svg class="abs shapes" viewBox="0 0 817 1200" aria-hidden="true">
    <polygon points="0,0 338,0 246,264 0,264" fill="#ffffff"/>
    <rect x="0" y="385" width="700" height="58" fill="#1d1d1f" opacity=".28"/>
    <polygon points="0,530 460,530 348,803 0,803" fill="var(--red)"/>
    <polygon points="442,530 817,530 817,586 420,586" fill="var(--blue)"/>
    <line x1="20" y1="563" x2="430" y2="563" stroke="#ffffff" stroke-width="2" stroke-dasharray="10 7"/>
  </svg>

  <div class="abs brand"><span class="brand-dot"></span><span class="brand-name">Kestrel</span></div>

  <div class="abs script-softball">softball</div>
  <div class="abs headline"><span class="summer">SUMMER</span><span class="camp">CAMP</span></div>
  <div class="abs year">2017</div>

  <div class="abs audience">for boys and girls</div>

  <div class="abs dates">Weeks of<br>July 10th - 14th<br>July 17th - 21st.</div>

  <div class="abs ages">
    <svg width="38" height="40" viewBox="0 0 38 40" aria-hidden="true">
      <circle cx="9" cy="5" r="4.5" fill="var(--blue)"/><rect x="4" y="11" width="10" height="14" rx="2" fill="var(--blue)"/>
      <rect x="5" y="24" width="3.5" height="14" fill="var(--blue)"/><rect x="9.5" y="24" width="3.5" height="14" fill="var(--blue)"/>
      <circle cx="28" cy="5" r="4.5" fill="var(--red)"/><polygon points="23,11 33,11 37,28 19,28" fill="var(--red)"/>
      <rect x="24" y="27" width="3" height="11" fill="var(--red)"/><rect x="29" y="27" width="3" height="11" fill="var(--red)"/>
    </svg>
    <div class="ages-label">Players<br>Ages</div>
  </div>
  <div class="abs ages-badge">5 - 11</div>

  <div class="abs hours">
    <svg width="30" height="34" viewBox="0 0 30 34" aria-hidden="true">
      <rect x="11" y="0" width="8" height="4" fill="var(--red)"/>
      <circle cx="15" cy="19" r="12" fill="none" stroke="var(--red)" stroke-width="3.5"/>
      <line x1="15" y1="19" x2="20" y2="13" stroke="var(--red)" stroke-width="3"/>
    </svg>
    <div class="hours-text">Full day = 9:30am - 2:30pm<br>Half day = 9:30am - 11:30am.</div>
  </div>
  <div class="abs cost">
    <span class="cost-label">Cost:</span>
    <svg width="32" height="32" viewBox="0 0 32 32" aria-hidden="true">
      <circle cx="16" cy="16" r="16" fill="var(--blue)"/>
      <text x="16" y="23" text-anchor="middle" font-family="Oswald, sans-serif" font-size="20" font-weight="600" fill="#fff">$</text>
    </svg>
    <div class="cost-text">$295 / Full day<br>$195/ half day</div>
  </div>

  <div class="abs rule-dashed" style="top:920px"></div>

  <div class="abs hosted">Hosted by "Kestrel Baseball"<br>Affiliated with the Harbor Comets Travel Baseball &amp; Softball Club and<br>the Maple Ridge Youth League</div>
  <div class="abs partner-comets" aria-hidden="true"></div>
  <div class="abs partner-league" aria-hidden="true"></div>

  <div class="abs rule-solid" style="top:1036px"></div>
  <div class="abs rule-dashed" style="top:1048px; left:0; width:817px"></div>

  <div class="abs register">Register<br>today!</div>

  <div class="abs block location">
    <div class="block-head">
      <svg width="18" height="24" viewBox="0 0 18 24" aria-hidden="true"><path d="M9 0C4 0 0 4 0 9c0 6 9 15 9 15s9-9 9-15c0-5-4-9-9-9z" fill="var(--blue)"/><circle cx="9" cy="9" r="3.5" fill="#fff"/></svg>
      Camp Location:
    </div>
    <div class="block-body">Camp location MRYL,<br>Route 9C Birch Hollow.</div>
  </div>

  <div class="abs block contact">
    <div class="block-head">
      <svg width="16" height="26" viewBox="0 0 16 26" aria-hidden="true"><rect x="5" y="0" width="2" height="6" fill="var(--blue)"/><rect x="1" y="6" width="14" height="20" rx="3" fill="var(--blue)"/><rect x="4" y="10" width="8" height="5" fill="#fff"/></svg>
      Contact:
    </div>
    <div class="block-body">Phone 555-240-7813, email<br>info@kestrelball.example</div>
  </div>
</div>
</body>
</html>
```